Custom Manufacturing Company square space website design

I own a custom manufacturing company that uses precision cutting technology to manufacture project components over a couple industries. We have an industrial CNC router and state of the art edge bander and cut a lot of cabinetry components for cabinet shops, builders, closet companies, ect. We offer design and assembly for any cabinetry or can build cabinets to spec. We also cut components for other industries out of wood, plastics, acryclics, ect. We offer design engineering services, product development protype services. we have a 3D printer farm. We want our communicate trust, dependability, and the value we place on client relationships.

We essentially want a credibility website. Landing page and drops downs for services we offer, capabilites, about us, contact

```html
<!DOCTYPE html>
<html lang="en">
<head>
<meta charset="utf-8">
<title>Northgate CNC – Precision Machining</title>
<link href="https://fonts.googleapis.com/css2?family=Oswald:wght@400;500;600&family=Mulish:wght@400;600&display=swap" rel="stylesheet">
<style>
:root{
  --ink:#1b1b1b;
  --dark:#1e1e1e;
  --charcoal:#2f2f2f;
  --panel:#333333;
  --light:#f1f1f1;
  --white:#ffffff;
  --muted:#6b6b6b;
  --line:#9a9a9a;
}
*{box-sizing:border-box;margin:0;padding:0}
html,body{width:1200px;height:4234px;overflow:hidden}
body{position:relative;background:var(--light);font-family:"Mulish",sans-serif;color:var(--ink)}
.abs{position:absolute}
.backdrop{position:absolute;left:0;top:0}
.head{font-family:"Oswald",sans-serif;font-weight:500;text-transform:uppercase}
.brand{font-family:"Oswald",sans-serif;font-weight:500;letter-spacing:3px;text-transform:uppercase;display:flex;align-items:center;gap:10px}
.brand .mark{width:22px;height:22px;background:currentColor}
.topbar{left:590px;top:28px;height:24px;display:flex;gap:34px;align-items:center;color:#ddd;font-family:"Oswald",sans-serif;font-size:13px}
.topbar span{display:flex;gap:6px;align-items:center}
.search{width:124px;border-bottom:1px solid #aaa;color:#999;display:flex;justify-content:space-between;padding-bottom:3px}
.nav{left:400px;top:79px;height:62px;right:0;display:flex;align-items:center;gap:34px;padding-left:38px;color:#fff;font-family:"Oswald",sans-serif;font-size:14px;text-transform:uppercase}
.nav .quote{margin-left:0;border:1.5px solid #fff;padding:9px 22px;font-weight:500}
.hero-title{left:0;width:1200px;top:248px;text-align:center;color:#fff;font-size:42px;line-height:49px}
.hero-sub{left:0;width:1200px;top:410px;text-align:center;color:#eee;font-size:15px}
.btn{display:flex;align-items:center;justify-content:center;background:var(--charcoal);color:#fff;font-family:"Oswald",sans-serif;font-weight:500;text-transform:uppercase;font-size:15px}
.btn.light{background:#fff;color:var(--ink)}
.section-title{left:0;width:1200px;text-align:center;font-size:31px}
.service{width:230px;text-align:center}
.service .pic{height:162px;position:relative}
.service p{margin-top:26px;font-family:"Oswald",sans-serif;font-size:13px;line-height:22px;text-transform:uppercase;padding:0 8px}
.project{width:256px;height:263px}
.project .pic{position:absolute;inset:0}
.project .cap{position:absolute;left:0;bottom:0;width:256px;height:91px}
.project .cap p{position:absolute;left:17px;top:20px;width:180px;color:#fff;font-family:"Oswald",sans-serif;font-size:12.5px;line-height:19px;text-transform:uppercase}
.arrow-box{width:39px;height:40px;background:#111;display:flex;align-items:center;justify-content:center}
.arrow-box.white{background:#fff}
.about-copy{left:161px;top:1700px;width:430px;color:#ddd;font-size:13px;line-height:28.6px}
.stat .num{font-family:"Oswald",sans-serif;font-size:34px;font-weight:500;margin-top:6px}
.stat .lbl{font-size:13px;color:#444;margin-top:4px}
.step{width:160px;text-align:center}
.step .ring{width:158px;height:158px;border-radius:50%;background:#fff;border:1.5px solid #d0d0d0;display:flex;align-items:center;justify-content:center}
.step p{margin-top:24px;font-family:"Oswald",sans-serif;font-size:16px;line-height:20px;text-transform:uppercase;font-weight:500}
.tile{height:198px;display:flex;flex-direction:column;align-items:center;justify-content:center;gap:26px;font-family:"Oswald",sans-serif;font-size:16px;font-weight:500;text-transform:uppercase}
.tile.on{background:#fff;color:var(--ink)}
.tile.off{background:#3a3a3a;color:#6e6e6e}
.field{width:216px}
.field label{font-size:11px;color:#777;display:block;padding-bottom:14px;border-bottom:1.5px solid var(--line)}
.contact-line{left:230px;color:#fff;font-size:14px;display:flex;gap:14px;align-items:flex-start}
.foot-links{top:4106px;font-size:13px;color:#ddd}
.social{width:22px;height:22px;border:1.5px solid #ccc}
</style>
</head>
<body>

<svg class="backdrop" width="1200" height="4234" viewBox="0 0 1200 4234">
  <defs>
    <linearGradient id="heroTone" x1="0" y1="0" x2="0" y2="1">
      <stop offset="0" stop-color="#2c2b1f"/>
      <stop offset="0.55" stop-color="#4a4a38"/>
      <stop offset="1" stop-color="#6a6a5c"/>
    </linearGradient>
  </defs>
  <rect x="0" y="0" width="1200" height="660" fill="url(#heroTone)" role="img" aria-label="Photo of a CNC laser cutter throwing sparks on a metal sheet"/>
  <rect x="0" y="0" width="1200" height="660" fill="#000" opacity="0.28"/>
  <polygon points="0,660 600,616 1200,660 1200,1500 0,1500" fill="#f1f1f1"/>
  <!-- what we do card with peak -->
  <polygon points="150,690 600,640 1050,690 1050,1021 150,1021" fill="#fff"/>
  <!-- about dark band -->
  <polygon points="0,1500 600,1554 1200,1500 1200,2071 600,1960 0,2071" fill="#1c1c1c"/>
  <!-- capabilities dark band -->
  <polygon points="0,2704 600,2778 1200,2704 1200,3247 600,3354 0,3247" fill="#1c1c1c"/>
  <!-- footer -->
  <rect x="0" y="3748" width="1200" height="486" fill="#1c1c1c"/>
  <!-- header logo panel -->
  <polygon points="0,0 386,0 330,148 0,148" fill="#fff"/>
  <polygon points="386,0 396,0 340,150 330,148" fill="#8a8a8a"/>
  <!-- nav bar -->
  <polygon points="400,79 1200,79 1200,141 381,141" fill="#1a1a1a" opacity="0.92"/>
  <line x1="0" y1="4156" x2="1200" y2="4156" stroke="#444" stroke-width="1" transform="scale(1)" />
</svg>

<!-- Header -->
<div class="abs brand" style="left:118px;top:56px;color:var(--ink);font-size:17px"><span class="mark"></span>Northgate CNC</div>
<div class="abs topbar">
  <span><svg width="12" height="12" viewBox="0 0 24 24" fill="none" stroke="#ddd" stroke-width="2"><path d="M5 3h4l2 5-3 2a12 12 0 0 0 6 6l2-3 5 2v4a2 2 0 0 1-2 2A18 18 0 0 1 3 5a2 2 0 0 1 2-2z"/></svg>(555) 014-2290</span>
  <span><svg width="13" height="11" viewBox="0 0 24 18" fill="none" stroke="#ddd" stroke-width="2"><rect x="1" y="1" width="22" height="16"/><path d="M1 1l11 9 11-9"/></svg>info@northgatecnc.com</span>
  <span class="search">SEARCH... <svg width="11" height="11" viewBox="0 0 24 24" fill="none" stroke="#fff" stroke-width="3"><circle cx="10" cy="10" r="7"/><path d="M15 15l7 7"/></svg></span>
</div>
<nav class="abs nav">
  <span>Home</span><span>About Us</span><span>Services &#8964;</span><span>Capabilities</span><span>Contact Us</span><span class="quote">Request a Quote</span>
</nav>

<!-- Hero -->
<h1 class="abs head hero-title">Looking for a reliable supplier for<br>CNC machining, production machining<br>services?</h1>
<p class="abs hero-sub">Providing high precision short run machining services for local industry in Western New York.</p>
<div class="abs btn" style="left:483px;top:447px;width:232px;height:63px;font-size:17px">Request a Quote</div>

<!-- What we do -->
<h2 class="abs head section-title" style="top:664px">What We Do</h2>
<div class="abs service" style="left:200px;top:741px">
  <div class="pic" role="img" aria-label="Cabinet design drawing on a monitor" style="background:linear-gradient(135deg,#e9eaec,#b7bcc2)"></div>
  <p>We offer design and assembly for any cabinetry or can build cabinets to specifications.</p>
</div>
<div class="abs service" style="left:485px;top:741px">
  <div class="pic" role="img" aria-label="Machinist cutting a component on a mill" style="background:linear-gradient(135deg,#3a4a5c,#1d2630)"></div>
  <p>We also cut components for other industries out of wood, plastics, acrylics, etc.</p>
</div>
<div class="abs service" style="left:771px;top:741px">
  <div class="pic" role="img" aria-label="Engineering prototype work at a bench" style="background:linear-gradient(135deg,#2a3f7a,#151c33)"></div>
  <p>We offer design engineering services, product development protype services.</p>
</div>

<!-- Recent projects -->
<h2 class="abs head section-title" style="top:1066px">Recent Projects</h2>
<div class="abs arrow-box" style="left:122px;top:1244px"><svg width="18" height="12" viewBox="0 0 18 12" fill="none" stroke="#fff" stroke-width="1.6"><path d="M17 6H2M7 1L2 6l5 5"/></svg></div>
<div class="abs arrow-box" style="left:1039px;top:1244px"><svg width="18" height="12" viewBox="0 0 18 12" fill="none" stroke="#fff" stroke-width="1.6"><path d="M1 6h15M11 1l5 5-5 5"/></svg></div>

<div class="abs project" style="left:196px;top:1146px">
  <div class="pic" role="img" aria-label="Worker grinding metal with sparks" style="background:linear-gradient(135deg,#6b5a48,#2b2520)"></div>
  <svg class="cap" viewBox="0 0 256 91"><polygon points="0,0 210,0 190,91 0,91" fill="#2a2a2a" opacity="0.92"/><polygon points="214,0 256,0 256,91 194,91" fill="#1a1a1a" opacity="0.92"/><path d="M220 68h17M232 63l5 5-5 5" stroke="#fff" stroke-width="1.5" fill="none"/></svg>
  <div class="cap"><p>Lorem ipsum dolor sit amet, consectetur adipiscing elit. Etiam suscipit lorem.</p></div>
</div>
<div class="abs project" style="left:472px;top:1146px">
  <div class="pic" role="img" aria-label="Milling machine with a tablet in hand" style="background:linear-gradient(135deg,#8a8d90,#3d4044)"></div>
  <svg class="cap" viewBox="0 0 256 91"><polygon points="0,0 210,0 190,91 0,91" fill="#2a2a2a" opacity="0.92"/><polygon points="214,0 256,0 256,91 194,91" fill="#1a1a1a" opacity="0.92"/><path d="M220 68h17M232 63l5 5-5 5" stroke="#fff" stroke-width="1.5" fill="none"/></svg>
  <div class="cap"><p>Lorem ipsum dolor sit amet, consectetur adipiscing elit. Etiam suscipit lorem.</p></div>
</div>
<div class="abs project" style="left:748px;top:1146px">
  <div class="pic" role="img" aria-label="Welder at a workstation" style="background:linear-gradient(135deg,#4a4f55,#22262b)"></div>
  <svg class="cap" viewBox="0 0 256 91"><polygon points="0,0 210,0 190,91 0,91" fill="#2a2a2a" opacity="0.92"/><polygon points="214,0 256,0 256,91 194,91" fill="#1a1a1a" opacity="0.92"/><path d="M220 68h17M232 63l5 5-5 5" stroke="#fff" stroke-width="1.5" fill="none"/></svg>
  <div class="cap"><p>Lorem ipsum dolor sit amet, consectetur adipiscing elit. Etiam suscipit lorem.</p></div>
</div>
<div class="abs btn" style="left:533px;top:1447px;width:134px;height:41px;font-size:14px">View All</div>

<!-- About -->
<h2 class="abs head" style="left:161px;top:1628px;font-size:34px;color:#fff">About Us</h2>
<p class="abs about-copy">Lorem ipsum dolor sit amet, consectetur adipiscing elit. Etiam suscipit lorem eget ligula tincidunt pharetra. Sed aliquam lacus et dolor tempus mollis. Etiam luctus, metus eget lobortis porttitor, arcu orci bibendum dolor, ut accumsan lacus nibh et nisi. Curabitur et pharetra orci. Sed vulputate erat risus. Sed lobortis nunc eleifend ornare ultrices. Mauris eget justo nisi. Nulla ultrices commodo orci ac vulputate. Nunc at leo quis elit tincidunt placerat. Nunc lacinia rutrum varius.</p>
<div class="abs btn light" style="left:161px;top:1953px;width:135px;height:40px;font-size:14px">Read More</div>
<div class="abs" role="img" aria-label="Engineer in a hard hat operating a CNC control panel" style="left:644px;top:1629px;width:356px;height:370px;background:linear-gradient(135deg,#c9ccd0,#5d6a86)"></div>

<!-- Stats -->
<div class="abs" style="left:150px;top:2030px;width:900px;height:193px;background:#fff"></div>
<div class="abs stat" style="left:196px;top:2060px">
  <svg width="44" height="38" viewBox="0 0 44 38" fill="none" stroke="#222" stroke-width="1.8"><rect x="2" y="10" width="40" height="26" rx="2"/><path d="M15 10V4h14v6M2 20h40M20 18v5h4v-5"/></svg>
  <div class="num">20+</div><div class="lbl">Years of Experience</div>
</div>
<div class="abs stat" style="left:411px;top:2060px">
  <svg width="44" height="38" viewBox="0 0 44 38" fill="none" stroke="#222" stroke-width="1.8"><path d="M6 2v36M6 4h26v18H6M10 9h18M10 14h18M10 18h18"/></svg>
  <div class="num">100%</div><div class="lbl">Made in America</div>
</div>
<div class="abs stat" style="left:625px;top:2060px">
  <svg width="44" height="38" viewBox="0 0 44 38" fill="none" stroke="#222" stroke-width="1.8"><circle cx="22" cy="19" r="17"/><path d="M8 12c6 2 8 6 6 10s2 8 6 12M26 3c-2 5 2 8 8 8M30 30c-2-4 0-8 6-8"/></svg>
  <div class="num">Global</div><div class="lbl">Servicimg &nbsp;the Globe</div>
</div>
<div class="abs stat" style="left:840px;top:2060px">
  <svg width="44" height="38" viewBox="0 0 44 38" fill="none" stroke="#222" stroke-width="1.8"><circle cx="22" cy="14" r="11"/><path d="M15 23l-4 13 6-3 3 4 2-9M29 23l4 13-6-3-3 4"/><path d="M17 14l4 4 7-7"/></svg>
  <div style="margin-top:8px;width:64px;height:26px;background:#222"></div>
  <div class="lbl" style="margin-top:10px">Industry Standatrds Met</div>
</div>

<!-- Process -->
<h2 class="abs head section-title" style="top:2310px">Our Process</h2>
<div class="abs step" style="left:200px;top:2395px">
  <div class="ring"><svg width="66" height="62" viewBox="0 0 66 62" fill="none" stroke="#222" stroke-width="2"><path d="M12 26a21 21 0 0 1 42 0H12zM8 26h50M33 5v10"/><circle cx="33" cy="46" r="9"/><path d="M33 33v4M33 55v4M20 46h4M42 46h4M24 37l3 3M39 52l3 3M42 37l-3 3M27 52l-3 3"/></svg></div>
  <p>Application<br>Engineering</p>
</div>
<div class="abs step" style="left:413px;top:2395px">
  <div class="ring"><svg width="66" height="62" viewBox="0 0 66 62" fill="none" stroke="#222" stroke-width="2"><path d="M33 6l28 13-28 13L5 19z"/><path d="M5 30l28 13 28-13M5 41l28 13 28-13"/></svg></div>
  <p>Material<br>Selection</p>
</div>
<div class="abs step" style="left:627px;top:2395px">
  <div class="ring"><svg width="66" height="62" viewBox="0 0 66 62" fill="none" stroke="#222" stroke-width="2"><path d="M6 8h54M28 4h10v12H28zM30 16l3 10 3-10M33 30v8M10 48h46M10 56h46M10 48v8M56 48v8"/></svg></div>
  <p>Part<br>Fabrication</p>
</div>
<div class="abs step" style="left:841px;top:2395px">
  <div class="ring"><svg width="70" height="52" viewBox="0 0 70 52" fill="none" stroke="#222" stroke-width="2"><path d="M18 8h30v30H18zM48 18h10l8 10v10H48"/><circle cx="26" cy="42" r="5"/><circle cx="56" cy="42" r="5"/><path d="M4 16h10M8 24h10M2 32h12"/></svg></div>
  <p>Delivery</p>
</div>
<svg class="abs" style="left:364px;top:2463px" width="42" height="20" viewBox="0 0 42 20" fill="#999"><path d="M0 2l8 8-8 8h6l8-8-8-8zM12 2l8 8-8 8h6l8-8-8-8zM24 2l8 8-8 8h6l8-8-8-8z"/></svg>
<svg class="abs" style="left:578px;top:2463px" width="42" height="20" viewBox="0 0 42 20" fill="#999"><path d="M0 2l8 8-8 8h6l8-8-8-8zM12 2l8 8-8 8h6l8-8-8-8zM24 2l8 8-8 8h6l8-8-8-8z"/></svg>
<svg class="abs" style="left:792px;top:2463px" width="42" height="20" viewBox="0 0 42 20" fill="#999"><path d="M0 2l8 8-8 8h6l8-8-8-8zM12 2l8 8-8 8h6l8-8-8-8zM24 2l8 8-8 8h6l8-8-8-8z"/></svg>
<div class="abs btn" style="left:533px;top:2650px;width:134px;height:40px;font-size:14px">Get Started</div>

<!-- Capabilities -->
<h2 class="abs head section-title" style="top:2864px;color:#fff">Our Capabilites</h2>
<div class="abs tile off" style="left:0;top:2934px;width:194px"><svg width="40" height="60" viewBox="0 0 40 60" fill="none" stroke="#6e6e6e" stroke-width="2"><path d="M4 4h32M14 4v12h12V4M16 16v24l4 16 4-16V16"/></svg>Reaming</div>
<div class="abs tile on" style="left:200px;top:2934px;width:195px"><svg width="60" height="64" viewBox="0 0 60 64" fill="none" stroke="#222" stroke-width="2"><path d="M6 4h48v10H6zM22 14h16v16H22zM30 30v8M8 50h44M8 58h44M8 50v8M52 50v8M24 44l6-4 6 4"/></svg>Parting/Cutting</div>
<div class="abs tile on" style="left:403px;top:2934px;width:192px"><svg width="60" height="64" viewBox="0 0 60 64" fill="none" stroke="#222" stroke-width="2"><circle cx="34" cy="34" r="16"/><circle cx="34" cy="34" r="4"/><path d="M4 4l26 26M6 58h50M10 50h40v8"/></svg>Facing</div>
<div class="abs tile on" style="left:603px;top:2934px;width:194px"><svg width="60" height="64" viewBox="0 0 60 64" fill="none" stroke="#222" stroke-width="2"><path d="M20 4v44M14 22h12v12H14zM4 56h52M8 48h44v8M34 40h12v8"/></svg>Turning</div>
<div class="abs tile on" style="left:804px;top:2934px;width:194px"><svg width="60" height="64" viewBox="0 0 60 64" fill="none" stroke="#222" stroke-width="2"><path d="M10 56h26v-8H10zM20 48L28 24l12 8M28 24l-6-12h10zM40 32l6 8"/><circle cx="48" cy="48" r="6"/></svg>Boring</div>
<div class="abs tile off" style="left:1006px;top:2934px;width:194px"><svg width="60" height="64" viewBox="0 0 60 64" fill="none" stroke="#6e6e6e" stroke-width="2"><path d="M24 4h12v10H24zM30 14v14M8 30h44v28H8zM8 44h44M20 30v28"/></svg>Drilling</div>
<div class="abs arrow-box" style="left:155px;top:3014px"><svg width="18" height="12" viewBox="0 0 18 12" fill="none" stroke="#fff" stroke-width="1.6"><path d="M17 6H2M7 1L2 6l5 5"/></svg></div>
<div class="abs arrow-box" style="left:1006px;top:3014px"><svg width="18" height="12" viewBox="0 0 18 12" fill="none" stroke="#fff" stroke-width="1.6"><path d="M1 6h15M11 1l5 5-5 5"/></svg></div>
<div class="abs btn light" style="left:533px;top:3170px;width:134px;height:39px;font-size:14px">Contact Us</div>

<!-- Contact -->
<h2 class="abs head section-title" style="top:3404px">Contact Us</h2>
<div class="abs" style="left:196px;top:3459px;width:802px;height:411px;background:#fff"></div>
<svg class="abs" style="left:196px;top:3459px" width="350" height="411" viewBox="0 0 350 411"><polygon points="0,0 169,0 347,411 0,411" fill="#333"/></svg>
<div class="abs brand" style="left:230px;top:3560px;color:#fff;font-size:16px"><span class="mark"></span>Northgate CNC</div>
<div class="abs contact-line" style="top:3642px"><svg width="16" height="16" viewBox="0 0 24 24" fill="#fff"><path d="M5 2h4l2 6-3 2a12 12 0 0 0 6 6l2-3 6 2v5a2 2 0 0 1-2 2A20 20 0 0 1 3 4a2 2 0 0 1 2-2z"/></svg>(555) 014-2290</div>
<div class="abs contact-line" style="top:3684px"><svg width="16" height="13" viewBox="0 0 24 18" fill="none" stroke="#fff" stroke-width="2"><rect x="1" y="1" width="22" height="16"/><path d="M1 1l11 9 11-9"/></svg>info@northgatecnc.com</div>
<div class="abs contact-line" style="top:3730px;line-height:20px"><svg width="14" height="18" viewBox="0 0 16 22" fill="#fff"><path d="M8 0a8 8 0 0 1 8 8c0 6-8 14-8 14S0 14 0 8a8 8 0 0 1 8-8zm0 5a3 3 0 1 0 0 6 3 3 0 0 0 0-6z"/></svg><span>123, Building Name, Street<br>City, State XY 123456</span></div>
<div class="abs" style="left:230px;top:3800px;color:#fff;font-size:13px;text-decoration:underline">VIEW DIRECTIONS</div>

<div class="abs field" style="left:515px;top:3525px"><label>First Name*</label></div>
<div class="abs field" style="left:751px;top:3525px"><label>Last Name*</label></div>
<div class="abs field" style="left:515px;top:3602px"><label>Phone Number*</label></div>
<div class="abs field" style="left:751px;top:3602px"><label>Postal Code*</label></div>
<div class="abs field" style="left:515px;top:3679px;width:452px"><label>Message*</label></div>
<div class="abs btn" style="left:850px;top:3757px;width:100px;height:39px;font-size:14px">Submit</div>

<!-- Footer -->
<div class="abs brand" style="left:0;width:1200px;justify-content:center;top:3996px;color:#fff;font-size:24px;letter-spacing:5px"><span class="mark" style="width:30px;height:30px"></span>Northgate CNC</div>
<div class="abs foot-links" style="left:243px">Home</div>
<div class="abs foot-links" style="left:385px">About Us</div>
<div class="abs foot-links" style="left:550px">Services</div>
<div class="abs foot-links" style="left:707px">Capabilities</div>
<div class="abs foot-links" style="left:887px">Contact Us</div>
<div class="abs" style="left:161px;top:4186px;color:#ccc;font-size:12px">© 2023 Northgate CNC. All Rights Reserved.</div>
<div class="abs" style="left:899px;top:4182px;display:flex;gap:16px"><span class="social"></span><span class="social"></span><span class="social"></span><span class="social"></span></div>

</body>
</html>
```